FinTech company looking to revamp and expand client-facing interface for our financial models

Pellworth Engines currently has a very simple website that allows clients to interact with our financial models. We are looking to completely redesign the current site and add several extra pages to provide extra functionality. We want the design to have a modern, slick feel, that will work on both a desktop or a tablet. It should be straightforward for clients to move between different pages at any time, and clear from the layout how to interact with the more advanced features. We have included screenshots of existing pages in the attached design brief, as well as sketches of the functionality required by the new pages, but can't provide a direct link to the current site.
Target Market(s)
Professional investors that will be paying to access the interface
Industry/Entity Type
Finance
Number of Pages Required
4 page
Colors
Designer to choose colors to be used in the design.
Look and feel
Each slider illustrates characteristics of the customer's brand and the style your logo design should communicate.

```html
<!DOCTYPE html>
<html lang="en">
<head>
<meta charset="utf-8">
<title>Pellworth Engines – Models and Factors</title>
<link rel="stylesheet" href="https://fonts.googleapis.com/css2?family=Poppins:wght@400;500;600&family=Open+Sans:wght@400&display=swap">
<style>
  :root {
    --backdrop: #6d6d6d;
    --panel: #ffffff;
    --nav-dark: #1b1b1b;
    --nav-mid: #262626;
    --nav-sub: #2a2a2a;
    --teal: #33b8a5;
    --teal-edge: #2a9f8f;
    --row-alt: #e6f4f1;
    --grid: #dcdcdc;
    --ink: #1e1e1e;
    --muted: #3a3a3a;
  }
  * { box-sizing: border-box; margin: 0; padding: 0; }
  html, body { width: 1186px; height: 1200px; overflow: hidden; }
  body {
    background: radial-gradient(ellipse at 50% 40%, #777 0%, var(--backdrop) 70%, #636363 100%);
    font-family: 'Poppins', sans-serif;
    color: var(--ink);
    position: relative;
  }
  .screen { position: absolute; background: var(--panel); }
  .screen--models { left: 98px; top: 94px; width: 989px; height: 508px; }
  .screen--factors { left: 178px; top: 676px; width: 830px; height: 433px; }

  .topbar { position: absolute; left: 0; right: 0; height: 43px; background: var(--nav-dark); color: #fff; font-weight: 600; font-size: 10.5px; }
  .topbar span, .topbar a { position: absolute; top: 0; line-height: 43px; color: #fff; text-decoration: none; white-space: nowrap; }
  .topbar .tab-active { background: var(--teal); width: 55px; text-align: center; }
  .topbar .brand { font-size: 11.5px; transform: translateX(-50%); }
  .topbar .current { background: var(--nav-mid); color: var(--teal); text-align: center; }
  .topbar .add-box { background: var(--nav-mid); width: 26px; text-align: center; color: var(--teal); font-size: 14px; }
  .topbar svg { vertical-align: -1px; margin-right: 3px; }

  .subbar { position: absolute; left: 0; right: 0; top: 65px; height: 37px; background: var(--nav-sub); color: #fff; font-weight: 500; font-size: 10px; }
  .subbar a { position: absolute; line-height: 37px; color: #fff; text-decoration: none; }

  .export { position: absolute; color: var(--teal); font-weight: 600; font-size: 10px; display: flex; align-items: center; gap: 3px; }

  .dropdown { position: absolute; background: var(--nav-dark); color: #fff; font-weight: 600; font-size: 10px; text-align: center; line-height: 27px; }

  table.data { position: absolute; border-collapse: collapse; table-layout: fixed; font-size: 10.5px; }
  table.data th {
    background: var(--teal); color: #fff; font-weight: 500; text-align: left;
    height: 43px; padding: 0 6px; position: relative; border-right: 1px solid #fff;
  }
  table.data th .sort {
    position: absolute; right: 0; top: 0; bottom: 0; width: 23px;
    border-left: 1px solid var(--teal-edge); border-right: 1px solid var(--teal-edge);
    display: flex; flex-direction: column; justify-content: space-between; align-items: center;
    padding: 4px 0 6px; font-size: 10px; line-height: 1;
  }
  table.data td { height: 44px; padding: 0 6px; border-right: 1px solid var(--grid); border-bottom: 1px solid var(--grid); font-weight: 400; color: var(--muted); line-height: 1.2; }
  table.data td:first-child { border-left: 1px solid var(--grid); }
  table.data td.label { font-weight: 500; color: var(--ink); }
  table.data tr.alt td { background: var(--row-alt); }
  .screen--factors table.data th { height: 41px; }

  .footer { position: absolute; left: 0; right: 0; text-align: center; font-family: 'Open Sans', sans-serif; font-size: 11px; color: #333; }
</style>
</head>
<body>

<section class="screen screen--models">
  <nav class="topbar" style="top:22px">
    <span style="left:21px">QCORE</span>
    <span class="tab-active" style="left:78px">250D</span>
    <span style="left:152px">83D</span>
    <span style="left:201px">42D</span>
    <span class="brand" style="left:415px">PELLWORTH</span>
    <span class="current" style="left:617px;width:84px">
      <svg width="10" height="9" viewBox="0 0 10 9"><path d="M5 0 L10 4.5 H8.5 V9 H6 V6 H4 V9 H1.5 V4.5 H0 Z" fill="currentColor"/></svg>MODELS</span>
    <span style="left:707px">
      <svg width="10" height="10" viewBox="0 0 10 10"><circle cx="5" cy="5" r="3.4" fill="none" stroke="#fff" stroke-width="1.2" stroke-dasharray="2 1"/><circle cx="5" cy="5" r="1.3" fill="none" stroke="#fff"/></svg>SENSITIVITIES</span>
    <span style="left:810px">|</span>
    <span style="left:828px">
      <svg width="10" height="10" viewBox="0 0 10 10"><path d="M5 0 L6.2 3.6 H10 L7 5.9 L8.1 9.6 L5 7.3 L1.9 9.6 L3 5.9 L0 3.6 H3.8 Z" fill="#fff"/></svg>FAVORITES</span>
    <span style="left:923px;font-size:14px">+</span>
  </nav>
  <nav class="subbar">
    <a style="left:442px">» EQUITIES</a>
    <a style="left:558px">» ETFS</a>
    <a style="left:656px">» PAIRS</a>
    <a style="left:760px">» ETF PAIRS</a>
    <a style="left:882px">» FACTORS</a>
  </nav>
  <div class="export" style="left:21px;top:117px">
    <svg width="10" height="9" viewBox="0 0 10 9"><rect x="0.6" y="0.6" width="5" height="7.8" fill="none" stroke="currentColor" stroke-width="1.2"/><path d="M4 4.5 H8 M6.5 2.5 L9 4.5 L6.5 6.5" stroke="currentColor" stroke-width="1.4" fill="none"/></svg>EXPORT
  </div>
  <table class="data" style="left:21px;top:145px;width:943px">
    <colgroup>
      <col style="width:60px"><col style="width:122px"><col style="width:83px"><col style="width:77px"><col style="width:77px"><col style="width:77px"><col style="width:73px"><col style="width:77px"><col style="width:77px"><col style="width:77px"><col style="width:77px"><col style="width:66px">
    </colgroup>
    <thead>
      <tr>
        <th>ID</th>
        <th>SECTOR<span class="sort"><b>+</b><b>–</b></span></th>
        <th>TIME<span class="sort"><b>+</b><b>–</b></span></th>
        <th>QUALITY<span class="sort"><b>+</b><b>–</b></span></th>
        <th>STAT 1<span class="sort"><b>+</b><b>–</b></span></th>
        <th>STAT 2<span class="sort"><b>+</b><b>–</b></span></th>
        <th>STAT 3<span class="sort"><b>+</b><b>–</b></span></th>
        <th>STAT 4<span class="sort"><b>+</b><b>–</b></span></th>
        <th>STAT 5<span class="sort"><b>+</b><b>–</b></span></th>
        <th>STAT 6<span class="sort"><b>+</b><b>–</b></span></th>
        <th>STAT 7<span class="sort"><b>+</b><b>–</b></span></th>
        <th>STAT 8<span class="sort"><b>+</b><b>–</b></span></th>
      </tr>
    </thead>
    <tbody>
      <tr><td class="label">Model 1</td><td class="label">Materials</td><td>2019-07-03<br>12:15:00.000</td><td>30.2288</td><td>2.01574</td><td>23.305</td><td>-0.149368</td><td>22.3054</td><td>4.63714</td><td>0.945706</td><td>2.81949</td><td>2.60858</td></tr>
      <tr class="alt"><td class="label">Model 2</td><td class="label">Industrials</td><td>2019-07-03<br>12:15:00.000</td><td>32.8694</td><td>0.87307</td><td>32.185</td><td>-0.0336927</td><td>33.9911</td><td>11.5693</td><td>-0.472968</td><td>-0.830458</td><td>6.80646</td></tr>
      <tr><td class="label">Model 3</td><td class="label">Consumer<br>Discretionary</td><td>2019-07-03<br>12:15:00.000</td><td>1.66002</td><td>-0.569222</td><td>159.814</td><td>0.0252328</td><td>172.616</td><td>10.2875</td><td>-0.750396</td><td>-0.385309</td><td>4.69146</td></tr>
      <tr class="alt"><td class="label">Model 4</td><td class="label">Information<br>Technology</td><td>2019-07-03<br>12:15:00.000</td><td>45.6856</td><td>0.412148</td><td>202.488</td><td>0.00849232</td><td>205.834</td><td>11.9094</td><td>-0.137913</td><td>0.449595</td><td>3.85106</td></tr>
      <tr><td class="label">Model 5</td><td class="label">Information<br>Technology</td><td>2019-07-03<br>12:15:00.000</td><td>75.7733</td><td>7.06728</td><td>188.605</td><td>0.016913</td><td>181.665</td><td>3.82241</td><td>0.981019</td><td>1.29847</td><td>3.34927</td></tr>
    </tbody>
  </table>
  <p class="footer" style="top:430px">© Copyrights 2019 Pellworth Engines | All Rights Reserved</p>
</section>

<section class="screen screen--factors">
  <nav class="topbar" style="top:19px">
    <span style="left:21px">FACTORS</span>
    <span class="tab-active" style="left:89px">250D</span>
    <span style="left:165px">83D</span>
    <span style="left:214px">42D</span>
    <span class="brand" style="left:391px">PELLWORTH</span>
    <span style="left:488px">
      <svg width="10" height="9" viewBox="0 0 10 9"><path d="M5 0 L10 4.5 H8.5 V9 H6 V6 H4 V9 H1.5 V4.5 H0 Z" fill="#fff"/></svg>MODELS</span>
    <span style="left:561px">|</span>
    <span style="left:571px">
      <svg width="10" height="10" viewBox="0 0 10 10"><circle cx="5" cy="5" r="3.4" fill="none" stroke="#fff" stroke-width="1.2" stroke-dasharray="2 1"/><circle cx="5" cy="5" r="1.3" fill="none" stroke="#fff"/></svg>SENSITIVITIES</span>
    <span style="left:674px">|</span>
    <span style="left:690px">
      <svg width="10" height="10" viewBox="0 0 10 10"><path d="M5 0 L6.2 3.6 H10 L7 5.9 L8.1 9.6 L5 7.3 L1.9 9.6 L3 5.9 L0 3.6 H3.8 Z" fill="#fff"/></svg>FAVORITES</span>
    <span class="add-box" style="left:784px">+</span>
  </nav>
  <div class="dropdown" style="left:707px;top:62px;width:103px">Add to</div>
  <div class="export" style="left:21px;top:72px">
    <svg width="10" height="9" viewBox="0 0 10 9"><rect x="0.6" y="0.6" width="5" height="7.8" fill="none" stroke="currentColor" stroke-width="1.2"/><path d="M4 4.5 H8 M6.5 2.5 L9 4.5 L6.5 6.5" stroke="currentColor" stroke-width="1.4" fill="none"/></svg>EXPORT
  </div>
  <table class="data" style="left:21px;top:94px;width:788px">
    <colgroup>
      <col style="width:83px"><col style="width:99px"><col style="width:96px"><col style="width:85px"><col style="width:85px"><col style="width:85px"><col style="width:85px"><col style="width:85px"><col style="width:85px">
    </colgroup>
    <thead>
      <tr>
        <th>FACTOR<span class="sort"><b>+</b><b>–</b></span></th>
        <th>ID<span class="sort"><b>+</b><b>–</b></span></th>
        <th>SECTOR<span class="sort"><b>+</b><b>–</b></span></th>
        <th>STAT 1<span class="sort"><b>+</b><b>–</b></span></th>
        <th>STAT 2<span class="sort"><b>+</b><b>–</b></span></th>
        <th>STAT 3<span class="sort"><b>+</b><b>–</b></span></th>
        <th>STAT 4<span class="sort"><b>+</b><b>–</b></span></th>
        <th>STAT 5<span class="sort"><b>+</b><b>–</b></span></th>
        <th>STAT 6<span class="sort"><b>+</b><b>–</b></span></th>
      </tr>
    </thead>
    <tbody>
      <tr><td class="label">Factor 1</td><td class="label">Model 1</td><td class="label">Materials</td><td>-1.4</td><td>0.1</td><td>-3.1</td><td>0.7</td><td>30.2</td><td>0.9</td></tr>
      <tr class="alt"><td class="label">Factor 2</td><td class="label">Model 1</td><td class="label">Materials</td><td>2.8</td><td>0.1</td><td>6.1</td><td>100</td><td>30.2</td><td>0.9</td></tr>
      <tr><td class="label">Factor 3</td><td class="label">Model 1</td><td class="label">Materials</td><td>-3.7</td><td>2.7</td><td>-7.2</td><td>100</td><td>30.2</td><td>0.9</td></tr>
      <tr class="alt"><td class="label">Factor 1</td><td class="label">Model 2</td><td class="label">Industrials</td><td>2.8</td><td>0.2</td><td>2.7</td><td>0.5</td><td>32.9</td><td>-0.5</td></tr>
      <tr><td class="label">Factor 2</td><td class="label">Model 2</td><td class="label">industrials</td><td>0.8</td><td>0.3</td><td>2.5</td><td>0.5</td><td>32.9</td><td>-0.5</td></tr>
    </tbody>
  </table>
  <p class="footer" style="top:406px">© Copyrights 2019 Pellworth Engines | All Rights Reserved</p>
</section>

</body>
</html>
```